Sophisticated, clean website reflecting my feminine, playful side to sell my abstract art,

I need a website no more than 3 pages to showcase my paintings, a little about me and some contact info. I do abstracts so looking for something a little edgy, yet feminine and current.
Updates

Hi there, These are some artists websites that I Iike: Marnelvoss.com (I like how airy it is) peterwallombry.com garethpolvens.com (I like how it scrolls) I'll need a place for a photo ( a headshot-i do not have it yet so I'll need to be able to upload that later) as well as an area for my bio. Also, it's important that I will be able to upload any new photos and descriptions easily so it should be user friendly. Lastly, I like in a sunny place so would like to have this seem upbeat and playful as that is how i like to paint. thanks-I'm trying to upload my photos now -

Target Market(s)

ppl ages 35-70 who want large scale art for their homes

Industry/Entity Type

art

Coding

Coded - Design and coding required

Number of Pages Required

3 page

Colors

Designer to choose colors to be used in the design.

Requirements
Must have
• photos of my art, a place for my bio, be easy to reach me. tasteful-nothing too "in your face" -my clients are pretty high end and organized. They like clean lines
Nice to have
• sophisticated background, muted tones in the back-similar clean font throughout-no cursive
Should not have
• too many dark areas. Too many blocks of color. Too serious.

```html
<!DOCTYPE html>
<html lang="en">
<head>
<meta charset="utf-8">
<title>Delia Marsh Art</title>
<link href="https://fonts.googleapis.com/css2?family=Caveat:wght@400;500&family=Lato:wght@400;700&family=Montserrat:wght@500;600&display=swap" rel="stylesheet">
<style>
:root{
  --magenta:#d63bbd;
  --magenta-deep:#c02aa6;
  --blush:#f7d3f0;
  --ink:#151515;
  --body:#2b2b2b;
  --white:#ffffff;
  --field:#fafafa;
  --black:#000000;
}
*{box-sizing:border-box;margin:0;padding:0}
html,body{width:1200px;height:3324px;overflow:hidden}
body{position:relative;background:var(--white);font-family:'Lato',sans-serif;color:var(--body)}
.abs{position:absolute}
.script{font-family:'Caveat',cursive;font-weight:400}
.heading{font-family:'Montserrat',sans-serif;font-weight:600;color:var(--ink)}
.center{text-align:center;left:0;width:1200px}
.tag{position:relative;display:inline-block;z-index:0}
.tag::after{content:"";position:absolute;right:-14px;top:50%;width:56%;height:40%;background:var(--magenta);opacity:.7;z-index:-1;transform:skewX(-14deg)}

/* header */
.site-header{top:0;left:0;width:1200px;height:88px;background:var(--white)}
.brand{left:112px;top:30px;font-family:'Montserrat',sans-serif;font-weight:600;font-size:21px;color:var(--ink)}
.nav{top:38px;left:0;font-size:15px;color:var(--ink)}
.nav a{position:absolute;white-space:nowrap;color:inherit;text-decoration:none}
.nav a.active{color:var(--magenta)}
.phone-chip{left:896px;top:27px;width:37px;height:37px;border-radius:50%;background:var(--magenta);display:flex;align-items:center;justify-content:center}
.phone-number{left:945px;top:36px;font-family:'Montserrat',sans-serif;font-weight:600;font-size:17px;color:var(--ink)}

/* hero */
.hero-art{top:87px;left:0;width:1200px;height:651px;background:radial-gradient(ellipse at 50% 45%,#d65ac6 0%,#c93fb6 55%,#b8309f 100%)}
.hero-welcome{top:244px;font-size:54px;color:var(--white)}
.hero-title{top:312px;font-size:56px;color:var(--white)}
.hero-text{top:383px;font-size:15.5px;line-height:26px;color:var(--white)}
.btn{display:flex;align-items:center;justify-content:center;border-radius:30px;font-family:'Caveat',cursive;font-weight:500;font-size:24px}
.btn-light{left:515px;top:455px;width:163px;height:53px;background:var(--white);color:var(--magenta)}

/* paintings */
.kicker{font-size:28px;color:var(--ink)}
.section-title{font-size:38px}
.card{width:302px;height:368px;background:var(--white);box-shadow:0 2px 14px rgba(0,0,0,.12);padding:9px;top:932px}
.card .painting{width:100%;height:100%}
.card-meta{top:1318px;width:302px;text-align:center}
.card-meta .label{font-size:22px;color:var(--magenta)}
.card-meta h3{font-family:'Montserrat',sans-serif;font-weight:500;font-size:23px;color:var(--ink);margin-top:0}
.card-meta p{font-size:15px;line-height:26px;margin-top:8px}

/* about */
.about-bg{top:1540px;left:0;width:1200px;height:620px;background:linear-gradient(180deg,#f9dcf3 0%,var(--blush) 50%,#f9dcf3 100%)}
.about-kicker{left:118px;top:1672px;font-size:28px;color:var(--ink)}
.about-title{left:112px;top:1712px;font-size:38px}
.about-text{left:112px;top:1766px;width:460px;font-size:16px;line-height:26px}
.btn-magenta{background:var(--magenta);color:var(--white)}
.about-btn{left:112px;top:1940px;width:155px;height:53px}
.about-frame{left:632px;top:1641px;width:455px;height:393px;background:var(--white);padding:10px}
.about-frame .painting{width:100%;height:100%}

/* contact */
.contact-text{top:2300px;left:310px;width:580px;text-align:center;font-size:15.5px;line-height:25px}
.field{background:var(--field);box-shadow:0 1px 8px rgba(0,0,0,.06);display:flex;align-items:flex-start;gap:8px;padding:15px 20px;font-size:15px;color:#555}
.field svg{flex:none;margin-top:2px}
.field-row{top:2376px;width:314px;height:51px}
.field-message{left:112px;top:2445px;width:976px;height:171px;padding-top:17px}
.send-btn{left:500px;top:2664px;width:186px;height:61px}

/* footer */
.site-footer{top:2806px;left:0;width:1200px;height:460px;background:var(--black)}
.footer-brand{top:2918px;font-family:'Montserrat',sans-serif;font-weight:600;font-size:27px;color:var(--white)}
.social{top:3016px;left:542px;display:flex;gap:12px}
.social span{width:16px;height:16px;border-radius:50%;background:var(--white)}
.footer-nav{top:3080px;font-size:15.5px;color:var(--white)}
.footer-nav a{position:absolute;color:inherit;text-decoration:none;white-space:nowrap}
.info{display:flex;gap:10px;align-items:flex-start;top:3142px;color:var(--white);font-size:15.5px;line-height:26px}
.info-dot{flex:none;width:36px;height:36px;border-radius:50%;background:#1f1f1f;display:flex;align-items:center;justify-content:center}
.copyright{top:3266px;left:0;width:1200px;height:58px;background:var(--magenta);display:flex;align-items:center;justify-content:center;color:var(--white);font-size:15.5px}
</style>
</head>
<body>

<header class="abs site-header">
  <div class="abs brand">Delia Marsh Art</div>
  <nav class="abs nav center">
    <a class="active" style="left:408px">Home</a>
    <a style="left:489px">About Us</a>
    <a style="left:592px">Our Blog</a>
    <a style="left:692px">Gallery</a>
    <a style="left:781px">Contact Us</a>
  </nav>
  <div class="abs phone-chip">
    <svg width="16" height="16" viewBox="0 0 24 24"><path fill="#fff" d="M6.6 10.8a15.1 15.1 0 0 0 6.6 6.6l2.2-2.2a1 1 0 0 1 1-.25 11.4 11.4 0 0 0 3.6.57 1 1 0 0 1 1 1V20a1 1 0 0 1-1 1A17 17 0 0 1 3 4a1 1 0 0 1 1-1h3.5a1 1 0 0 1 1 1c0 1.25.2 2.45.57 3.57a1 1 0 0 1-.25 1z"/></svg>
  </div>
  <div class="abs phone-number">+1 888 888 8888</div>
</header>

<section>
  <div class="abs hero-art" role="img" aria-label="Abstract magenta ink painting as hero background"></div>
  <div class="abs center hero-welcome script"><span class="tag">Welcome To</span></div>
  <h1 class="abs center heading hero-title" style="color:var(--white)">Delia Marsh Art</h1>
  <p class="abs center hero-text">Lorem ipsum dolor sit amet, consectetur adipiscing elit, sed do eiusmod tempor incididunt ut<br>labore et dolore magna aliqua. Quis ipsum suspendisse ultrices gravida.</p>
  <div class="abs btn btn-light">Get stared</div>
</section>

<section>
  <div class="abs center script kicker" style="top:808px"><span class="tag">Delia Marsh Art</span></div>
  <h2 class="abs center heading section-title" style="top:850px">My Painting</h2>

  <div class="abs card" style="left:112px"><div class="painting" role="img" aria-label="Abstract floral painting in blue, gold and orange" style="background:linear-gradient(160deg,#e8e4d6,#c9b98a)"></div></div>
  <div class="abs card" style="left:453px"><div class="painting" role="img" aria-label="Abstract floral painting in green and charcoal" style="background:linear-gradient(160deg,#9fb8a6,#4f6f5a)"></div></div>
  <div class="abs card" style="left:794px"><div class="painting" role="img" aria-label="Abstract floral painting in brown and blush" style="background:linear-gradient(160deg,#e9dfda,#b08a7a)"></div></div>

  <div class="abs card-meta" style="left:112px"><div class="label script">Lorem Ipsum</div><h3>Delia Marsh Art</h3><p>Lorem ipsum dolor sit amet, consec-<br>tetur adipiscing elit, sed do eiusmod<br>tempor incididunt ut</p></div>
  <div class="abs card-meta" style="left:453px"><div class="label script">Lorem Ipsum</div><h3>Delia Marsh Art</h3><p>Lorem ipsum dolor sit amet, consec-<br>tetur adipiscing elit, sed do eiusmod<br>tempor incididunt ut</p></div>
  <div class="abs card-meta" style="left:794px"><div class="label script">Lorem Ipsum</div><h3>Delia Marsh Art</h3><p>Lorem ipsum dolor sit amet, consec-<br>tetur adipiscing elit, sed do eiusmod<br>tempor incididunt ut</p></div>
</section>

<section>
  <div class="abs about-bg" role="img" aria-label="Soft pale pink brushed paint texture background"></div>
  <div class="abs about-kicker script"><span class="tag">About Us</span></div>
  <h2 class="abs heading about-title">Delia Marsh Art</h2>
  <p class="abs about-text">Lorem ipsum dolor sit amet, consectetur adipiscing elit, sed do eiusmod tempor incididunt ut labore et dolore magna aliqua. Quis ipsum suspendisse ultrices gravida. Risus commodo viverra maecenas accumsan lacus vel facilisis.Lorem ipsum dolor sit amet, consectetur adipiscing elit, sed do eiusmod tempor incididunt ut labore et dolore magna aliqua.</p>
  <div class="abs btn btn-magenta about-btn">Learn More</div>
  <div class="abs about-frame"><div class="painting" role="img" aria-label="Abstract painting in teal and blue tones on wood" style="background:radial-gradient(ellipse at 50% 50%,#3f9a90 0%,#6f8aa0 100%)"></div></div>
</section>

<section>
  <div class="abs center script kicker" style="top:2208px"><span class="tag">Get A Quote</span></div>
  <h2 class="abs center heading section-title" style="top:2246px">Contact Us</h2>
  <p class="abs contact-text">Lorem ipsum dolor sit amet, consectetur adipiscing elit, sed do eiusmod tempor incididunt ut labore et dolore magna aliqua.</p>

  <div class="abs field field-row" style="left:112px"><svg width="14" height="14" viewBox="0 0 24 24" fill="none" stroke="#555" stroke-width="2"><circle cx="12" cy="8" r="4"/><path d="M4 21c0-4 4-6 8-6s8 2 8 6"/></svg>Name</div>
  <div class="abs field field-row" style="left:442px"><svg width="14" height="14" viewBox="0 0 24 24" fill="none" stroke="#555" stroke-width="2"><rect x="3" y="5" width="18" height="14" rx="1"/><path d="M3 6l9 7 9-7"/></svg>Email</div>
  <div class="abs field field-row" style="left:773px"><svg width="14" height="14" viewBox="0 0 24 24" fill="none" stroke="#555" stroke-width="2"><path d="M6.6 10.8a15 15 0 0 0 6.6 6.6l2.2-2.2 5 1.4V20A17 17 0 0 1 3 4h3.6l1.3 4.8z"/></svg>Phone</div>
  <div class="abs field field-message"><svg width="14" height="14" viewBox="0 0 24 24" fill="none" stroke="#555" stroke-width="2"><path d="M4 5h16v11H9l-5 4z"/></svg>Message</div>
  <div class="abs btn btn-magenta send-btn">Send Message</div>
</section>

<footer>
  <div class="abs site-footer"></div>
  <div class="abs center footer-brand">Delia Marsh Art</div>
  <div class="abs social"><span></span><span></span><span></span><span></span><span></span></div>
  <nav class="abs footer-nav center">
    <a style="left:374px">Home</a>
    <a style="left:456px">About Us</a>
    <a style="left:559px">Our Blog</a>
    <a style="left:659px">Gallery</a>
    <a style="left:749px">Contact Us</a>
  </nav>
  <div class="abs info" style="left:226px"><span class="info-dot"><svg width="12" height="14" viewBox="0 0 24 28"><path fill="#d63bbd" d="M12 0a10 10 0 0 0-10 10c0 7 10 18 10 18s10-11 10-18A10 10 0 0 0 12 0zm0 14a4 4 0 1 1 0-8 4 4 0 0 1 0 8z"/></svg></span><span style="padding-top:5px">Lorem ipsum dolor sit amet,<br>consectetur adipiscing</span></div>
  <div class="abs info" style="left:518px"><span class="info-dot"><svg width="14" height="12" viewBox="0 0 24 20"><path fill="#d63bbd" d="M0 2l12 8 12-8V0H0zm0 3v15h24V5l-12 8z"/></svg></span><span style="padding-top:5px">info@deliamarshart.com</span></div>
  <div class="abs info" style="left:808px"><span class="info-dot"><svg width="13" height="13" viewBox="0 0 24 24"><path fill="#d63bbd" d="M6.6 10.8a15.1 15.1 0 0 0 6.6 6.6l2.2-2.2a1 1 0 0 1 1-.25 11.4 11.4 0 0 0 3.6.57 1 1 0 0 1 1 1V20a1 1 0 0 1-1 1A17 17 0 0 1 3 4a1 1 0 0 1 1-1h3.5a1 1 0 0 1 1 1c0 1.25.2 2.45.57 3.57a1 1 0 0 1-.25 1z"/></svg></span><span style="padding-top:5px">+1 888 888 8888</span></div>
  <div class="abs copyright">©Copyrights 2022&nbsp;&nbsp; Delia Marsh Art &nbsp;&nbsp;|&nbsp;&nbsp; All Rights Reserved</div>
</footer>

</body>
</html>
```